Harborview Estates Business Card for Apartment Buildings

Create business cards for resident managers who run apartment buildings. The audience is the public who are searching for apartment rentals, and current residents who live at the apartment building. Key design element will be incorporating the company logo, however, the logo cannot dominate. The building name and manager name are more important than the logo. Current business card design leaves little room for copy, so we may need to reduce the size on the current card to allow for more space for copy.

Target Market(s)

Adults 18-65 years of age, who are looking for an apartment rental, plus current residents who live at our apartment buildings.

Industry/Entity Type

Property Management

Contact Information for Business Card

A major design element will be use of the company logo. Important property and manager contact information must be part of the design. The size of the logo will need to be reduced to make room for building and manager contact copy.

Font styles to use
Sans Serif

Colors
3176b5
000000
959595
ffffff

Requirements
Must have
• 1) Incorporate the company logo.
• 2) Use the company colors (dark blue, black/grey, over white).
• 3) FEATURE THE BUILDING NAME
• 4) FEATURE THE MANAGER NAME
• 5) The company name is less important than BUILDING and MANAGER
• 6) Manager contact information
• **SEE ATTACHED CREATIVE BRIEF**
Nice to have
• 1) Back of card logo watermark
• 2) Ability to write notes on back of carfd
Should not have
• Avoid letting the company logo dominate the card, the building name and manager are more important than the company logo.

```html
<!DOCTYPE html>
<html lang="en">
<head>
<meta charset="utf-8">
<title>Harborview Estates Business Card</title>
<link href="https://fonts.googleapis.com/css2?family=Oswald:wght@600&family=Lato:wght@400;700;900&display=swap" rel="stylesheet">
<style>
  :root {
    --brand-blue: #1b6fae;
    --ink: #3a3a3c;
    --grey: #959595;
    --white: #ffffff;
    --backdrop: #2a2a2a;
  }
  html, body { margin: 0; padding: 0; overflow: hidden; }
  body {
    width: 1200px; height: 852px;
    background: var(--backdrop);
    position: relative;
    font-family: "Lato", sans-serif;
  }
  .card {
    position: absolute;
    width: 560px; height: 320px;
    border-radius: 18px;
    overflow: hidden;
    box-shadow: 0 18px 40px rgba(0,0,0,.55);
  }
  /* Back of card */
  .card-back {
    left: 70px; top: 110px;
    background: var(--brand-blue);
  }
  .card-back .watermark {
    position: absolute; left: 95px; top: 30px;
    width: 260px; height: 260px; border-radius: 50%;
    border: 10px solid rgba(255,255,255,.09);
    box-sizing: border-box;
  }
  .card-back .wordmark {
    position: absolute; left: 0; right: 0; top: 110px;
    display: flex; align-items: center; justify-content: center; gap: 16px;
  }
  .card-back .wordmark-dot {
    width: 54px; height: 54px; border-radius: 50%;
    background: var(--white);
  }
  .card-back .wordmark-name {
    color: var(--white);
    font-weight: 900; font-size: 38px; line-height: 1;
    letter-spacing: 1px; text-transform: uppercase;
  }
  .card-back .web {
    position: absolute; left: 0; right: 0; bottom: 52px;
    text-align: center; color: var(--white);
    font-size: 15px; letter-spacing: .5px;
  }
  /* Front of card */
  .card-front {
    left: 570px; top: 420px;
    background: var(--white);
  }
  .card-front .swoosh { position: absolute; inset: 0; width: 560px; height: 320px; }
  .card-front .emblem {
    position: absolute; right: 50px; top: 24px;
    width: 170px; height: 170px; border-radius: 50%;
    border: 12px solid var(--ink);
    box-sizing: border-box;
  }
  .card-front .tab {
    position: absolute; left: 0; top: 66px;
    width: 10px; height: 34px; background: var(--brand-blue);
  }
  .manager-name {
    position: absolute; left: 34px; top: 56px; margin: 0;
    font-family: "Oswald", sans-serif; font-weight: 600;
    font-size: 28px; line-height: 40px; color: var(--brand-blue);
    letter-spacing: .5px; text-transform: uppercase;
  }
  .manager-title {
    position: absolute; left: 36px; top: 96px; margin: 0;
    font-size: 14px; line-height: 18px; color: var(--ink);
  }
  .contacts {
    position: absolute; left: 36px; top: 132px;
    list-style: none; margin: 0; padding: 0;
    font-size: 14px; color: var(--ink); line-height: 18px;
  }
  .contacts li { display: flex; align-items: center; gap: 10px; }
  .contacts svg { width: 11px; height: 11px; fill: var(--brand-blue); flex: none; }
  .building {
    position: absolute; left: 36px; top: 228px;
    font-size: 13px; line-height: 16px; color: var(--ink);
    font-style: normal;
  }
  .building-name {
    display: block; color: var(--brand-blue);
    font-weight: 700; font-size: 16px; line-height: 20px;
  }
</style>
</head>
<body>

<section class="card card-back">
  <div class="watermark"></div>
  <div class="wordmark">
    <div class="wordmark-dot"></div>
    <div class="wordmark-name">Harborview Estates</div>
  </div>
  <div class="web">www.harborviewest.com</div>
</section>

<section class="card card-front">
  <svg class="swoosh" viewBox="0 0 560 320">
    <path d="M0 306 L420 306 Q450 306 462 262 Q472 228 505 228 L560 228 L560 320 L0 320 Z" fill="var(--brand-blue)"/>
    <path d="M0 292 L400 292 Q428 292 440 258 Q448 236 470 230" fill="none" stroke="var(--ink)" stroke-width="5"/>
  </svg>
  <div class="emblem"></div>
  <div class="tab"></div>
  <h1 class="manager-name">Marisol Delgado</h1>
  <p class="manager-title">Resident Manager</p>
  <ul class="contacts">
    <li><svg viewBox="0 0 12 12"><path d="M2 1h3l1 3-2 1a7 7 0 0 0 3 3l1-2 3 1v3c0 1-1 1-1 1A10 10 0 0 1 1 2s0-1 1-1z"/></svg>555-204-1180</li>
    <li><svg viewBox="0 0 12 12"><rect x="1" y="3" width="10" height="7" rx="1"/><rect x="3" y="1" width="6" height="3"/></svg>555-318-4472</li>
    <li><svg viewBox="0 0 12 12"><path d="M3 0h6a1 1 0 0 1 1 1v10a1 1 0 0 1-1 1H3a1 1 0 0 1-1-1V1a1 1 0 0 1 1-1zm0 2v7h6V2z"/></svg>555-640-2915</li>
    <li><svg viewBox="0 0 12 12"><path d="M0 2h12v8H0zm1 1v.5l5 3.5 5-3.5V3z"/></svg>marisol@harborviewest.com</li>
    <li><svg viewBox="0 0 12 12"><circle cx="6" cy="6" r="5.5"/></svg>www.harborviewest.com</li>
  </ul>
  <address class="building">
    <span class="building-name">Cedar Crest Apartments</span>
    1428 Linden Avenue<br>
    Lakeport, CA 94012
  </address>
</section>

</body>
</html>
```